Resort Room Letter to go in Welcome Basket

It needs the Resort Logo and a snazzier font. Probably some kind of background. It will be in full color. Dimensions 5.5in x 8in. This is the in room letter that goes with the welcome basket.

Text:

Welcome to The Resort! We have prepared this convenient Starter Pack to enhance your stay in our Luxury Condominiums. To further enhance your stay housekeeping will provide daily limited service which includes fresh towels and trash removal. Additional housekeeping services can be scheduled with the front desk for a nominal fee. Please leave the basket so that we can prepare a Starter Pack for the next guest. When you are ready to checkout simply dial **47.

Helpful Hints:

Turn the lever in the freezer to start making ice
The Waterpark can be accessed from the 1st Floor
The Indoor Waterpark is open from 9AM to 11PM
Vending with Snacks & Drinks are available on Floors 1, 2, 4, & 5
The closest grocery store is Brindlemart
You can also conveniently order groceries via Pantrygo from Halvey, Grain Town, & Tressa
Additional convenience items are available for purchase at the Front Desk
Use our Express Checkout by Dialing **47

Thank you so much for choosing the Resort for your Smoky Mountain Vacation!

The Resort Management Team

```html
<!DOCTYPE html>
<html lang="en">
<head>
<meta charset="utf-8">
<title>Welcome Letter – Laurel Bend Resort</title>
<link href="https://fonts.googleapis.com/css2?family=Titillium+Web:wght@300;400;700&family=Mrs+Saint+Delafield&display=swap" rel="stylesheet">
<style>
  :root {
    --teal-dark: #2e8c80;
    --teal-light: #4ea69a;
    --white: #ffffff;
    --frame: #eef0ef;
    --ink: #2b2b2b;
    --gold: #c99a62;
    --brown: #6b4a33;
    --steel: #a7aaa6;
    --dash: #4a5a57;
  }
  * { margin: 0; padding: 0; box-sizing: border-box; }
  html, body { width: 847px; height: 1200px; overflow: hidden; background: var(--white); }
  .letter {
    position: relative; width: 847px; height: 1200px; overflow: hidden;
    background: linear-gradient(135deg, var(--teal-dark) 0%, var(--teal-light) 100%);
    font-family: "Titillium Web", sans-serif; color: var(--white);
  }
  .door-frame { position: absolute; left: 0; top: 0; width: 60px; height: 1200px; background: var(--frame); }
  .trim-line { position: absolute; inset: 0; }
  .hanger { position: absolute; left: 107px; top: 0; }
  .welcome-script {
    position: absolute; left: 72px; top: 150px;
    font-family: "Mrs Saint Delafield", cursive; font-size: 118px; line-height: 1;
    color: var(--gold);
  }
  .welcome-sub { position: absolute; left: 128px; top: 278px; font-size: 28px; color: var(--ink); font-weight: 400; }
  .brand { position: absolute; font-weight: 700; color: var(--brown); text-align: center; line-height: 1.1; }
  .brand-hanger { left: 130px; top: 360px; width: 172px; font-size: 24px; }
  .brand-footer { left: 640px; top: 1050px; width: 150px; font-size: 20px; }
  .intro {
    position: absolute; left: 366px; top: 240px; width: 285px;
    font-size: 14.6px; font-weight: 300; line-height: 21.6px; text-align: justify;
  }
  .peephole { position: absolute; left: 662px; top: 288px; }
  .handle { position: absolute; left: 56px; top: 740px; }
  .hints { position: absolute; left: 214px; top: 560px; list-style: none; width: 500px; }
  .hints li { display: flex; gap: 12px; font-size: 19.5px; font-weight: 300; line-height: 24px; margin-bottom: 23px; }
  .hints svg { flex: none; width: 32px; height: 26px; }
  .thanks { position: absolute; left: 170px; top: 1026px; width: 460px; font-size: 18.5px; font-weight: 700; line-height: 24px; }
  .signoff { position: absolute; left: 170px; top: 1097px; font-size: 18.5px; font-weight: 700; }
</style>
</head>
<body>
<main class="letter">
  <div class="door-frame"></div>
  <svg class="trim-line" width="847" height="1200">
    <rect x="38" y="36" width="778" height="1129" fill="none" stroke="var(--dash)" stroke-width="1.5" stroke-dasharray="10 7"/>
    <path d="M694 272 V192 H222 V520 H694 V356" fill="none" stroke="var(--white)" stroke-width="5"/>
  </svg>

  <svg class="hanger" width="218" height="494" viewBox="0 0 218 494">
    <path d="M0 176 V0 H218 V478 a14 14 0 0 1 -14 14 H14 a14 14 0 0 1 -14 -14 Z" fill="var(--white)"/>
    <path d="M0 176 C0 108 38 96 52 110 C36 60 70 32 110 32 C150 32 178 60 178 100 C178 140 150 160 110 160 C80 160 60 160 50 176 Z" fill="var(--teal-dark)" opacity="0"/>
    <path d="M38 110 a12 12 0 0 1 -12 -12 C26 50 66 18 110 18 C156 18 192 52 192 100 C192 150 160 176 110 176 H0 V492" fill="none"/>
    <path d="M0 0 H52 V96 C46 60 76 32 112 32 C150 32 178 62 178 100 C178 140 150 176 112 176 H0 Z" fill="var(--teal-dark)"/>
    <path d="M58 110 C50 70 78 48 112 48 C146 48 166 72 166 100 C166 132 144 162 112 162 H58 Z" fill="var(--white)" opacity="0"/>
  </svg>

  <div class="welcome-script">Welcome</div>
  <div class="welcome-sub">to The Resort!</div>
  <div class="brand brand-hanger">Laurel Bend<br>Resort</div>

  <p class="intro">We have prepared this convenient Starter Pack to enhance your stay in our Luxury Condominiums. To further enhance your stay housekeeping will provide daily limited service which includes fresh towels and trash removal. Additional housekeeping services can be scheduled with the front desk for a nominal fee. Please leave the basket so that we can prepare a Starter Pack for the next guest. When you are ready to checkout simply dial **47.</p>

  <svg class="peephole" width="50" height="50" role="img" aria-label="Door peephole">
    <circle cx="25" cy="25" r="24" fill="var(--steel)"/>
    <circle cx="25" cy="25" r="12" fill="#6d706d"/>
  </svg>

  <svg class="handle" width="92" height="400" role="img" aria-label="Brushed steel door handle with lock">
    <rect x="0" y="0" width="92" height="400" rx="46" fill="var(--steel)"/>
  </svg>

  <ul class="hints">
    <li><svg viewBox="0 0 32 26"><rect x="2" y="6" width="28" height="14" rx="4" fill="none" stroke="#fff" stroke-width="1.5"/><circle cx="16" cy="13" r="4" fill="none" stroke="#fff" stroke-width="1.5"/></svg>Turn the lever in the freezer to start making ice</li>
    <li><svg viewBox="0 0 32 26"><path d="M6 2 V24 M6 6 H22 L26 12 H10 M10 16 H26" fill="none" stroke="#fff" stroke-width="1.5"/></svg>The Waterpark can be accessed from the 1st Floor</li>
    <li><svg viewBox="0 0 32 26"><circle cx="16" cy="4" r="2.5" fill="#fff"/><path d="M16 8 V16 M9 10 H23 M4 19 q3 -3 6 0 t6 0 t6 0 t6 0 M4 23 q3 -3 6 0 t6 0 t6 0 t6 0" fill="none" stroke="#fff" stroke-width="1.5"/></svg>The Indoor Waterpark is open from 9AM to 11PM</li>
    <li><svg viewBox="0 0 32 26"><path d="M2 20 H30 L27 24 H5 Z M6 20 V6 H14 V20 M16 20 L20 10 H28 V20" fill="none" stroke="#fff" stroke-width="1.5"/></svg>Vending with Snacks &amp; Drinks are available on Floors 1, 2, 4, &amp; 5</li>
    <li><svg viewBox="0 0 32 26"><path d="M4 8 H28 V25 H4 Z M6 2 H26 L28 8 H4 Z M9 14 H17 V20 H9 Z" fill="none" stroke="#fff" stroke-width="1.5"/></svg>The closest grocery store is Brindlemart</li>
    <li><svg viewBox="0 0 32 26"><path d="M7 10 H25 L23 25 H9 Z M12 10 L14 2 M18 10 L20 3" fill="none" stroke="#fff" stroke-width="1.5"/></svg>You can also conveniently order groceries via Pantrygo from Halvey, Grain Town, &amp; Tressa</li>
    <li><svg viewBox="0 0 32 26"><path d="M2 12 H30 V25 H2 Z M2 16 H30" fill="none" stroke="#fff" stroke-width="1.5"/><circle cx="16" cy="6" r="3" fill="none" stroke="#fff" stroke-width="1.5"/></svg>Additional convenience items are available for purchase at the Front Desk</li>
    <li><svg viewBox="0 0 32 26"><rect x="6" y="2" width="20" height="22" rx="2" fill="none" stroke="#fff" stroke-width="1.5"/><path d="M10 7 H22 M10 13 H12 M15 13 H17 M20 13 H22 M10 18 H12 M15 18 H17 M20 18 H22" stroke="#fff" stroke-width="1.5"/></svg>Use our Express Checkout by Dialing **47</li>
  </ul>

  <p class="thanks">Thank you so much for choosing the Resort for your Smoky Mountain Vacation!</p>
  <p class="signoff">The Resort Management Team</p>
  <div class="brand brand-footer">Laurel Bend<br>Resort</div>
</main>
</body>
</html>
```